Easy Marinade Labels for Butchery Store

Need a set of labels designed for a Butchery Shop. They will sit in the top left corner of the packets as a triangle (7cm each side). Easy because the only major requirement is the label name and some small text saying "Please ask in store to see spec sheet for ingredients". Extra points for finding a fun way to incorporate the logo and/or images of food (garlic bulbs, chilli, spices ect) to enhance the label. List of Marinade Names below: GarlicPepper Mint & RosemarySatayBBQChilli Plum & GingerSundried Tomato & BasilBuffaloHoney SoyHoi-SinPer PeriSpicy CajunTeriyakiBlack Bean Ive also attached the logo and an example of how the label might sit on a packet of meat. Thanks

Target Market(s)

Butchery Deli Shop Customers

Industry/Entity Type

Food Store

Font styles to use
Serif
Sans Serif
Decorative
Other font styles liked:
• Fun font that isn't a generic Quellbrix Font?

Colors

Designer to choose colors to be used in the design.

Requirements
Must have
• Product Name
• Small text saying "Please ask in store to see spec sheet for ingredients"
Nice to have
• Photos of ingredients that would match that type of marinade - Chilli, Garlic, Spices.
• Fenly Oak Logo - not essential if it doesn't look good on the label / doesn't fit.

```html
<!DOCTYPE html>
<html lang="en">
<head>
<meta charset="utf-8">
<title>Hoisin Marinade Label</title>
<link rel="stylesheet" href="https://fonts.googleapis.com/css2?family=Amatic+SC:wght@700&family=Fira+Sans:wght@700&display=swap">
<style>
  :root {
    --paper: #ffffff;
    --frame-yellow: #f2ea1e;
    --leaf-green: #7fae3a;
    --deep-green: #2f4a1c;
    --sauce-orange: #c9703e;
    --glaze-amber: #e58a2e;
    --chilli-red: #a8282a;
    --label-ink: #ffffff;
    --shadow-ink: #1a1a1a;
  }
  html, body {
    margin: 0;
    padding: 0;
    width: 1200px;
    height: 900px;
    overflow: hidden;
    background: var(--paper);
  }
  .canvas {
    position: relative;
    width: 1200px;
    height: 900px;
  }
  .label-shape {
    position: absolute;
    left: 0;
    top: 0;
  }
  .label-title {
    position: absolute;
    left: 378px;
    top: 196px;
    margin: 0;
    font-family: "Amatic SC", "Arial Narrow", sans-serif;
    font-weight: 700;
    font-size: 156px;
    line-height: 1;
    letter-spacing: 0.09em;
    color: var(--label-ink);
    text-shadow: 4px 4px 0 var(--shadow-ink);
  }
  .label-note {
    position: absolute;
    left: 352px;
    top: 448px;
    margin: 0;
    font-family: "Fira Sans", Arial, sans-serif;
    font-weight: 700;
    font-size: 21px;
    line-height: 30px;
    letter-spacing: 0.12em;
    color: var(--label-ink);
    text-transform: uppercase;
  }
</style>
</head>
<body>
<div class="canvas">
  <svg class="label-shape" width="1200" height="900" viewBox="0 0 1200 900">
    <defs>
      <linearGradient id="ingredient-tones" x1="0" y1="0" x2="0.35" y2="1">
        <stop offset="0" stop-color="var(--leaf-green)"/>
        <stop offset="0.18" stop-color="var(--deep-green)"/>
        <stop offset="0.38" stop-color="var(--sauce-orange)"/>
        <stop offset="0.55" stop-color="var(--glaze-amber)"/>
        <stop offset="0.72" stop-color="var(--sauce-orange)"/>
        <stop offset="1" stop-color="var(--chilli-red)"/>
      </linearGradient>
    </defs>
    <polygon class="label-photo" role="img"
      aria-label="Photo of fresh marinade ingredients: green herbs, sweet potato, orange squash and red chillies"
      points="319,149 988,149 319,820" fill="url(#ingredient-tones)"/>
    <polygon class="label-frame" points="319,149 988,149 319,820"
      fill="none" stroke="var(--frame-yellow)" stroke-width="8" stroke-linejoin="miter"/>
  </svg>
  <h1 class="label-title">HOISIN</h1>
  <p class="label-note">Please ask in store<br>to see spec sheet<br>for ingredients</p>
</div>
</body>
</html>
```